Fernhale Business Card Design

We are looking for a fresh business card design for our new logo. We would like a business card that is unique but friendly. We are in the window coverings business offering blinds, shutters and shades for homes.

Target Market(s)

Targeting the end-consumer

Industry/Entity Type

Business

Requirements
Must have
• Must have a dedicates space for a photo of our sales person. Must contain our new logo (attached).

```html
<!DOCTYPE html>
<html lang="en">
<head>
<meta charset="utf-8">
<title>Fernhale Business Card</title>
<link rel="stylesheet" href="https://fonts.googleapis.com/css2?family=Poppins:wght@400;500&display=swap">
<style>
  :root {
    --page-bg: #d8d4cf;
    --card-bg: #eef0ec;
    --card-edge: #dfe2dc;
    --brand-green: #7ab648;
    --band-green: #8cc152;
    --ink-dark: #4a4a4a;
    --ink-grey: #6e6e6e;
    --band-text: #f4f8ef;
    --photo-light: #d9d3cc;
    --photo-dark: #3b3634;
  }
  * { box-sizing: border-box; margin: 0; padding: 0; }
  html, body {
    width: 1200px; height: 1047px; overflow: hidden;
    background: var(--page-bg);
    font-family: "Poppins", sans-serif;
  }
  .card {
    position: absolute; left: 80px; top: 241px;
    width: 1040px; height: 565px;
    background: var(--card-bg);
    border: 1px solid var(--card-edge);
    border-radius: 24px;
    overflow: hidden;
  }
  .brand {
    position: absolute; left: 62px; top: 48px;
    display: flex; align-items: center; gap: 24px;
  }
  .brand-mark {
    width: 96px; height: 96px;
    background: var(--brand-green);
    border-radius: 6px;
  }
  .brand-name {
    font-size: 60px; font-weight: 500; color: var(--ink-dark);
    letter-spacing: 0.5px;
  }
  .person-name {
    position: absolute; left: 62px; top: 226px;
    font-size: 29px; font-weight: 500; color: var(--brand-green);
    letter-spacing: 1.5px; text-transform: uppercase;
  }
  .person-role {
    position: absolute; left: 62px; top: 264px;
    font-size: 23px; font-weight: 400; color: var(--ink-grey);
    letter-spacing: 1px; text-transform: uppercase;
  }
  .contact-list {
    position: absolute; left: 62px; top: 326px;
    list-style: none;
  }
  .contact-item {
    display: flex; align-items: center;
    height: 33px;
    font-size: 21px; color: var(--ink-grey); letter-spacing: 0.5px;
  }
  .contact-icon {
    width: 20px; height: 20px; margin-right: 28px;
    fill: var(--brand-green);
  }
  .address-band {
    position: absolute; left: 0; bottom: 0;
    width: 560px; height: 54px;
    background: var(--band-green);
    display: flex; align-items: center; padding-left: 58px;
    font-size: 20px; color: var(--band-text); letter-spacing: 0.5px;
  }
  .salesperson-photo {
    position: absolute; left: 560px; top: 0;
    width: 480px; height: 565px;
    background: linear-gradient(180deg, var(--photo-light) 0%, #9c8f86 45%, var(--photo-dark) 100%);
  }
</style>
</head>
<body>
  <section class="card">
    <div class="brand">
      <div class="brand-mark"></div>
      <div class="brand-name">Fernhale</div>
    </div>

    <h1 class="person-name">Dana Whitfield</h1>
    <p class="person-role">Realtor</p>

    <ul class="contact-list">
      <li class="contact-item">
        <svg class="contact-icon" viewBox="0 0 24 24"><path d="M6.6 10.8a15 15 0 0 0 6.6 6.6l2.2-2.2a1 1 0 0 1 1-.25 11.4 11.4 0 0 0 3.6.57 1 1 0 0 1 1 1V20a1 1 0 0 1-1 1A17 17 0 0 1 3 4a1 1 0 0 1 1-1h3.5a1 1 0 0 1 1 1c0 1.25.2 2.45.57 3.6a1 1 0 0 1-.25 1z"/></svg>
        (014) 552-0193
      </li>
      <li class="contact-item">
        <svg class="contact-icon" viewBox="0 0 24 24"><path d="M7 1h10a2 2 0 0 1 2 2v18a2 2 0 0 1-2 2H7a2 2 0 0 1-2-2V3a2 2 0 0 1 2-2zm0 3v14h10V4zm5 15.5a1.2 1.2 0 1 0 0 2.4 1.2 1.2 0 0 0 0-2.4z"/></svg>
        (014) 552-0193
      </li>
      <li class="contact-item">
        <svg class="contact-icon" viewBox="0 0 24 24"><path d="M6 2h12v6H6zM4 9h16a2 2 0 0 1 2 2v6h-4v5H6v-5H2v-6a2 2 0 0 1 2-2zm4 6v5h8v-5z"/></svg>
        (014) 552-0193
      </li>
      <li class="contact-item">
        <svg class="contact-icon" viewBox="0 0 24 24"><path d="M2 5h20v14H2zm2 2v.5l8 5 8-5V7l-8 5z"/></svg>
        info@fernhalehome.com
      </li>
      <li class="contact-item">
        <svg class="contact-icon" viewBox="0 0 24 24"><path d="M12 2a10 10 0 1 0 0 20 10 10 0 0 0 0-20zm6.9 6h-3a15 15 0 0 0-1.3-3.6A8 8 0 0 1 18.9 8zM12 4c.8 1.1 1.5 2.5 1.9 4h-3.8c.4-1.5 1.1-2.9 1.9-4zM4.3 14a8 8 0 0 1 0-4h3.4a16 16 0 0 0 0 4zm.8 2h3a15 15 0 0 0 1.3 3.6A8 8 0 0 1 5.1 16zm3-8h-3a8 8 0 0 1 4.3-3.6A15 15 0 0 0 8.1 8zM12 20c-.8-1.1-1.5-2.5-1.9-4h3.8c-.4 1.5-1.1 2.9-1.9 4zm2.3-6H9.7a14 14 0 0 1 0-4h4.6a14 14 0 0 1 0 4zm.3 5.6A15 15 0 0 0 15.9 16h3a8 8 0 0 1-4.3 3.6zM16.3 14a16 16 0 0 0 0-4h3.4a8 8 0 0 1 0 4z"/></svg>
        www.fernhalehome.com
      </li>
    </ul>

    <div class="address-band">P.O.Box: 482, Lindell Bay, Avonmere</div>

    <div class="salesperson-photo" role="img" aria-label="Photo of the salesperson, smiling, arms crossed, in a dark blazer"></div>
  </section>
</body>
</html>
```